Zenqo - revolutionary mobile payment

The app is a P2P money trasfert, without the using of credit card or bank circuits it can transfer electronic money from one person to another consumers simply and immediatelly.
You can use the color you want, but the message we need to transert to consumer is simplicity, safety and coolness.
In attach the logo of the company and the wireframe of thre page of the app.
The goal is to design the page of the app with a clear, simple and intuitive graphic.
Updates

I have upgrade the brief with important information and detail, many thanks

Target Market(s)

all the people

Industry/Entity Type

Credit Card

Requirements
Must have
• You have to design one icon for each button in the first page, (shop is: where to shop)
in the second one a new intuitive image (instead of the hand) that let the user to understand that with a simple swipe he can process the payment
Nice to have
• You can include or esxclude what you want or belive can improve user experience of the app
Should not have
• too much color, too much button or information

```html
<!DOCTYPE html>
<html lang="en">
<head>
<meta charset="utf-8">
<title>Zenqo – Home</title>
<link rel="stylesheet" href="https://fonts.googleapis.com/css2?family=Roboto:wght@300;400&display=swap">
<style>
  :root {
    --backdrop: #eeedf1;
    --header-blue: #3d5689;
    --main-navy: #1b3264;
    --profile-band: #eef0f3;
    --profile-text: #2c3d63;
    --white: #ffffff;
    --icon-navy: #1b3264;
    --avatar-tone: #c9a08a;
  }
  * { margin: 0; padding: 0; box-sizing: border-box; }
  html, body {
    width: 897px; height: 1200px; overflow: hidden;
    background: var(--backdrop);
    font-family: "Roboto", "Helvetica Neue", Arial, sans-serif;
  }
  .app-screen {
    position: absolute; left: 120px; top: 20px;
    width: 656px; height: 1161px;
    background: var(--main-navy);
    overflow: hidden;
  }
  .app-header {
    position: absolute; left: 0; top: 0; width: 100%; height: 138px;
    background: var(--header-blue); color: var(--white);
  }
  .status-bar {
    position: absolute; left: 0; top: 0; width: 100%; height: 46px;
    font-size: 22px; font-weight: 400;
  }
  .status-signal { position: absolute; left: 14px; top: 14px; }
  .status-time { position: absolute; left: 0; right: 0; top: 10px; text-align: center; }
  .status-battery { position: absolute; right: 12px; top: 10px; display: flex; align-items: center; gap: 8px; }
  .account-number {
    position: absolute; left: 19px; top: 72px;
    font-size: 27px; font-weight: 400; letter-spacing: 0.2px;
  }
  .settings-button { position: absolute; left: 581px; top: 62px; width: 52px; height: 52px; }
  .profile-band {
    position: absolute; left: 0; top: 138px; width: 100%; height: 116px;
    background: var(--profile-band);
    border-bottom: 3px solid #22355f;
  }
  .profile-avatar {
    position: absolute; left: 23px; top: 16px; width: 84px; height: 84px;
    border-radius: 50%; background: radial-gradient(circle at 50% 40%, #e6c3ae, var(--avatar-tone) 60%, #6b4a3a);
  }
  .plan-name {
    position: absolute; left: 127px; top: 40px;
    font-size: 27px; font-weight: 400; color: var(--profile-text);
  }
  .action {
    position: absolute; width: 211px; text-align: center; color: var(--white);
  }
  .action-disc {
    width: 211px; height: 211px; border-radius: 50%;
    background: var(--white);
    display: flex; align-items: center; justify-content: center;
  }
  .action-label {
    display: block; margin-top: 38px;
    font-size: 58px; font-weight: 300; letter-spacing: -1.5px; line-height: 1;
  }
  .action-pay { left: 60px; top: 326px; }
  .action-ask { left: 372px; top: 326px; }
  .action-account { left: 60px; top: 767px; }
  .action-shop { left: 372px; top: 767px; }
</style>
</head>
<body>
<main class="app-screen">
  <header class="app-header">
    <div class="status-bar">
      <svg class="status-signal" width="70" height="18" viewBox="0 0 70 18">
        <g fill="#fff"><circle cx="6" cy="9" r="5"/><circle cx="19" cy="9" r="5"/><circle cx="32" cy="9" r="5"/></g>
        <g fill="none" stroke="#fff" stroke-width="1.3"><circle cx="45" cy="9" r="4.4"/><circle cx="58" cy="9" r="4.4"/></g>
      </svg>
      <svg style="position:absolute;left:92px;top:12px" width="24" height="18" viewBox="0 0 24 18">
        <g fill="none" stroke="#fff" stroke-width="2.4" stroke-linecap="round">
          <path d="M2 6.5a14 14 0 0 1 20 0"/><path d="M6 10.5a8.5 8.5 0 0 1 12 0"/>
        </g>
        <circle cx="12" cy="15" r="2.4" fill="#fff"/>
      </svg>
      <div class="status-time">4:39 PM</div>
      <div class="status-battery">
        <span>100%</span>
        <svg width="48" height="20" viewBox="0 0 48 20">
          <rect x="1" y="2" width="42" height="16" rx="2" fill="none" stroke="#fff" stroke-width="1.5"/>
          <rect x="3.5" y="4.5" width="37" height="11" fill="#fff"/>
          <rect x="44" y="7" width="3" height="6" fill="#fff"/>
        </svg>
      </div>
    </div>
    <div class="account-number">+321456780219</div>
    <svg class="settings-button" viewBox="0 0 52 52" aria-label="Settings">
      <g fill="none" stroke="#fff" stroke-width="2">
        <path d="M22 4h8l1.5 6 4.5 2 5.3-3.2 5.7 5.7-3.2 5.3 2 4.5 6 1.5v8l-6 1.5-2 4.5 3.2 5.3-5.7 5.7-5.3-3.2-4.5 2L30 48h-8l-1.5-6-4.5-2-5.3 3.2-5.7-5.7 3.2-5.3-2-4.5L0 30v-8l6-1.5 2-4.5-3.2-5.3 5.7-5.7L15.8 8.2l4.7-2z" transform="translate(1 0) scale(0.96)"/>
        <circle cx="26" cy="26" r="8"/>
      </g>
    </svg>
  </header>

  <section class="profile-band">
    <div class="profile-avatar" role="img" aria-label="Profile photo of the account holder"></div>
    <span class="plan-name">Basic</span>
  </section>

  <nav>
    <a class="action action-pay">
      <div class="action-disc">
        <svg width="122" height="78" viewBox="0 0 122 78" fill="none" stroke="var(--icon-navy)" stroke-width="5">
          <polyline points="16,10 16,4 118,4 118,62 112,62"/>
          <polyline points="8,18 8,12 110,12 110,70 104,70"/>
          <rect x="3" y="20" width="98" height="55"/>
          <text x="52" y="63" text-anchor="middle" font-family="Roboto, sans-serif" font-weight="400" font-size="42" fill="var(--icon-navy)" stroke="none">$</text>
        </svg>
      </div>
      <span class="action-label">Pay</span>
    </a>
    <a class="action action-ask">
      <div class="action-disc">
        <svg width="100" height="92" viewBox="0 0 100 92" fill="none" stroke="var(--icon-navy)" stroke-width="5">
          <polyline points="58,44 4,44 4,88 94,88 94,54"/>
          <line x1="16" y1="60" x2="52" y2="60"/>
          <line x1="16" y1="72" x2="52" y2="72"/>
          <path d="M74 8l14 8-24 42-12 6 0-14z" stroke-linejoin="round"/>
          <line x1="78" y1="4" x2="96" y2="14"/>
          <line x1="58" y1="76" x2="80" y2="76"/>
        </svg>
      </div>
      <span class="action-label">Ask</span>
    </a>
    <a class="action action-account">
      <div class="action-disc">
        <svg width="112" height="84" viewBox="0 0 112 84" fill="none" stroke="var(--icon-navy)" stroke-width="5">
          <rect x="3" y="3" width="106" height="78" rx="3"/>
          <line x1="3" y1="22" x2="109" y2="22"/>
          <g fill="var(--icon-navy)" stroke="none"><circle cx="14" cy="13" r="3.5"/><circle cx="24" cy="13" r="3.5"/><circle cx="34" cy="13" r="3.5"/></g>
          <path d="M47 50v-7a9 9 0 0 1 18 0v7"/>
          <rect x="43" y="50" width="26" height="20"/>
          <line x1="56" y1="57" x2="56" y2="64"/>
        </svg>
      </div>
      <span class="action-label">Account</span>
    </a>
    <a class="action action-shop">
      <div class="action-disc">
        <svg width="84" height="104" viewBox="0 0 84 104" fill="none" stroke="var(--icon-navy)" stroke-width="5">
          <path d="M42 100L16 70A36 36 0 1 1 68 70z" fill="var(--icon-navy)" stroke="none"/>
          <circle cx="42" cy="42" r="30" fill="var(--white)" stroke="none"/>
          <path d="M24 28h36l4 12H20z" stroke-width="4"/>
          <line x1="33" y1="28" x2="31" y2="40" stroke-width="4"/>
          <line x1="42" y1="28" x2="42" y2="40" stroke-width="4"/>
          <line x1="51" y1="28" x2="53" y2="40" stroke-width="4"/>
          <rect x="24" y="44" width="36" height="14" stroke-width="4"/>
        </svg>
      </div>
      <span class="action-label">Shop</span>
    </a>
  </nav>
</main>
</body>
</html>
```